Delegate visit agenda

We need a creative, yet simple and official design for an agenda to be handed out for delegates visiting our organization. The design needs to be creative, informative and visual when possible. Flat design is desired but other options are welcomed. The agenda should be 3 pages in lengths only. Page 1 should have the company logo with an event title (with the ability to add country flag) and the dates of the event. Pages 2 should include photos of receiving delegate (e.g. VIPs) and any other relevant people. Page 3 should include agenda entries with the following information: title of entry, date and time, location, relevant pictures (e.g. a hotel or flight). The generic style of an infographic.
Updates
Project Deadline Extended
Reason: Not enough submissions received.
No optimal design (i.e. creative and attractive) received.

Brief has been updated with samples.

Target Market(s)
Very high profile people (e.g. presidents, ministers, GM,...etc.)
Industry/Entity Type
Hotel
Colors
Designer to choose colors to be used in the design.
Look and feel
Each slider illustrates characteristics of the customer's brand and the style your logo design should communicate.

```html
<!DOCTYPE html>
<html lang="en">
<head>
<meta charset="utf-8">
<title>Delegate Visit Agenda</title>
<link rel="stylesheet" href="https://fonts.googleapis.com/css2?family=Source+Sans+3:ital,wght@0,400;0,600;0,700;1,400;1,600&display=swap">
<style>
  :root{
    --bg-light:#fbf6ee;
    --bg-mid:#f1e2cc;
    --bg-warm:#e9d2b3;
    --gold:#b8862b;
    --ink:#1d1d1d;
    --text:#3a3a3a;
    --white:#ffffff;
    --brand:#5a8f1e;
  }
  *{box-sizing:border-box;margin:0;padding:0}
  html,body{width:1200px;height:849px;overflow:hidden}
  body{font-family:"Source Sans 3",Arial,sans-serif;color:var(--text)}
  .page{position:relative;width:1200px;height:849px;overflow:hidden;
    background:linear-gradient(125deg,var(--bg-light) 0%,var(--bg-mid) 30%,var(--bg-light) 55%,var(--bg-warm) 100%)}
  .route{position:absolute;left:0;top:0}
  .title{position:absolute;left:114px;top:70px;font-size:30px;font-weight:700;color:var(--ink);letter-spacing:.5px}
  .intro{position:absolute;left:114px;top:116px;width:162px}
  h3{font-size:13px;font-weight:700;color:var(--ink);line-height:1.15}
  .sub{font-size:10px;font-weight:600;color:var(--ink);line-height:1.3;margin-bottom:6px}
  p{font-size:11px;line-height:14.6px;text-align:justify;color:var(--text)}
  .stop{position:absolute;border-radius:50%;background:var(--white);border:3px solid var(--gold);
    box-shadow:2px 4px 8px rgba(90,60,20,.3)}
  .stop .body{position:absolute}
  .icon{position:absolute;width:26px;height:20px}
  .marker{position:absolute;width:54px;height:54px;margin:-27px 0 0 -27px;border-radius:50%;
    background:var(--ink);color:var(--white);text-align:center;z-index:3}
  .marker::after{content:"";position:absolute;left:20px;bottom:-6px;width:12px;height:12px;background:var(--ink);transform:rotate(45deg)}
  .marker .day{display:block;font-size:23px;font-weight:700;line-height:1;margin-top:8px}
  .marker .time{display:block;font-size:10px;font-style:italic;line-height:1.2}
  .brand{position:absolute;right:34px;top:74px;display:flex;align-items:center;gap:8px;
    font-size:24px;font-weight:700;color:var(--brand)}
  .brand .dot{width:16px;height:16px;border-radius:50%;background:var(--brand)}
  .legend{position:absolute;top:795px;left:0;width:1200px;height:30px}
  .legend .item{position:absolute;display:flex;align-items:center;gap:8px;font-size:12px;color:var(--ink)}
  .legend svg{width:32px;height:30px}
</style>
</head>
<body>
<div class="page">

  <svg width="0" height="0" style="position:absolute">
    <defs>
      <symbol id="ic-gears" viewBox="0 0 32 30">
        <circle cx="10" cy="11" r="6" fill="none" stroke="#1d1d1d" stroke-width="4" stroke-dasharray="2.4 1.6"/>
        <circle cx="10" cy="11" r="4.5" fill="#1d1d1d"/><circle cx="10" cy="11" r="1.8" fill="#fff"/>
        <circle cx="21" cy="20" r="6" fill="none" stroke="#1d1d1d" stroke-width="4" stroke-dasharray="2.4 1.6"/>
        <circle cx="21" cy="20" r="4.5" fill="#1d1d1d"/><circle cx="21" cy="20" r="1.8" fill="#fff"/>
      </symbol>
      <symbol id="ic-chat" viewBox="0 0 32 30">
        <rect x="2" y="4" width="20" height="12" rx="2" fill="#1d1d1d"/>
        <path d="M6 16 l-1 5 l5 -5z" fill="#1d1d1d"/>
        <rect x="10" y="11" width="20" height="12" rx="2" fill="#fff" stroke="#1d1d1d" stroke-width="1.5"/>
        <path d="M25 23 l2 4 l-5 -4z" fill="#fff" stroke="#1d1d1d" stroke-width="1.2"/>
      </symbol>
      <symbol id="ic-cloche" viewBox="0 0 32 30">
        <circle cx="16" cy="8" r="2" fill="#1d1d1d"/>
        <path d="M4 22 A12 12 0 0 1 28 22 Z" fill="#1d1d1d"/>
        <rect x="2" y="23" width="28" height="3" rx="1" fill="#1d1d1d"/>
      </symbol>
      <symbol id="ic-flower" viewBox="0 0 32 30">
        <g fill="#fff" stroke="#1d1d1d" stroke-width="1.4">
          <circle cx="16" cy="5" r="3.5"/><circle cx="16" cy="25" r="3.5"/>
          <circle cx="6" cy="15" r="3.5"/><circle cx="26" cy="15" r="3.5"/>
          <circle cx="9" cy="8" r="3"/><circle cx="23" cy="8" r="3"/>
          <circle cx="9" cy="22" r="3"/><circle cx="23" cy="22" r="3"/>
        </g>
        <circle cx="16" cy="15" r="6" fill="#1d1d1d"/>
      </symbol>
      <symbol id="ic-globe" viewBox="0 0 32 30">
        <g fill="none" stroke="#1d1d1d" stroke-width="1.5">
          <circle cx="16" cy="15" r="12"/>
          <ellipse cx="16" cy="15" rx="5" ry="12"/>
          <line x1="16" y1="3" x2="16" y2="27"/>
          <line x1="4" y1="15" x2="28" y2="15"/>
          <path d="M6 9 H26 M6 21 H26"/>
        </g>
      </symbol>
    </defs>
  </svg>

  <svg class="route" width="1200" height="849" viewBox="0 0 1200 849">
    <path d="M282 95 C330 100 380 110 440 122 C490 130 540 145 570 160 C590 172 610 180 624 184 C700 210 760 240 800 265 C830 290 850 305 862 313 C900 340 960 390 1016 438 C1060 480 1090 560 1080 650 C1070 720 1000 752 908 753 C850 752 760 730 700 711 C650 692 560 650 500 620 C470 605 440 595 413 582 C370 560 330 530 306 512 C280 492 262 472 239 461 C220 450 200 440 180 430"
      fill="none" stroke="#b8862b" stroke-width="5" stroke-linecap="round" stroke-dasharray="0 10"/>
    <g fill="#fbf6ee" stroke="#1d1d1d" stroke-width="2.5">
      <circle cx="408" cy="113" r="5"/><circle cx="624" cy="184" r="5"/>
      <circle cx="862" cy="313" r="5"/><circle cx="1016" cy="438" r="5"/>
      <circle cx="908" cy="753" r="5"/><circle cx="700" cy="711" r="5"/>
      <circle cx="413" cy="582" r="5"/><circle cx="239" cy="461" r="5"/>
      <circle cx="306" cy="512" r="5"/>
    </g>
  </svg>

  <h1 class="title">AGENDA</h1>
  <div class="intro">
    <h3>Lorem ipsum</h3>
    <div class="sub">LOREM IPSUM</div>
    <p>Lorem ipsum dolor sit amet, error regione voluptua mea ei, ei ullum civibus efficiantur pri. Ei exerci reprimique has. Duo te dicant complectitur, pri ei nihil munere doctus. Vix id exerci verear, mea ea accusata petentium ullamcorper. Vel offendit percipit</p>
  </div>

  <div class="brand"><span class="dot"></span>Telvora</div>

  <div class="stop" style="left:446px;top:28px;width:146px;height:146px">
    <svg class="icon" style="left:112px;top:36px"><use href="#ic-cloche"/></svg>
    <div class="body" style="left:24px;top:20px;width:104px">
      <h3>Lorem ipsum</h3><div class="sub">LOREM IPSUM</div>
      <p>Lorem ipsum dolor sit amet, error regione voluptua mea ei, ei ullum civibus</p>
    </div>
  </div>

  <div class="stop" style="left:662px;top:71px;width:200px;height:200px">
    <svg class="icon" style="left:124px;top:32px"><use href="#ic-chat"/></svg>
    <div class="body" style="left:32px;top:27px;width:144px">
      <h3>Lorem ipsum</h3><div class="sub">LOREM IPSUM</div>
      <p>Lorem ipsum dolor sit amet, error regione voluptua mea ei, ei ullum civibus efficiantur pri. Ei exerci reprimique has. Duo te dicant complectitur, pri ei nihil munere doctus. Vix id exerci</p>
    </div>
  </div>

  <div class="stop" style="left:903px;top:226px;width:172px;height:168px">
    <svg class="icon" style="left:118px;top:12px"><use href="#ic-flower"/></svg>
    <div class="body" style="left:23px;top:10px;width:132px">
      <h3>Lorem ipsum</h3><div class="sub">LOREM IPSUM</div>
      <p>Lorem ipsum dolor sit amet, error regione voluptua mea ei, ei ullum civibus efficiantur pri. Ei exerci reprimique has. Duo te dicant complectitur, pri ei</p>
    </div>
  </div>

  <div class="stop" style="left:900px;top:478px;width:184px;height:184px">
    <svg class="icon" style="left:118px;top:22px"><use href="#ic-gears"/></svg>
    <div class="body" style="left:26px;top:24px;width:134px">
      <h3>Lorem ipsum</h3><div class="sub">LOREM IPSUM</div>
      <p>Lorem ipsum dolor sit amet, error regione voluptua mea ei, ei ullum civibus efficiantur pri. Ei exerci reprimique has. Duo te dicant complectitur, pri ei</p>
    </div>
  </div>

  <div class="stop" style="left:763px;top:598px;width:146px;height:146px">
    <div class="body" style="left:19px;top:22px;width:98px">
      <h3>Lorem ipsum</h3><div class="sub">LOREM IPSUM</div>
      <p>Lorem ipsum dolor sit amet, error regione voluptua mea ei, ei ullum</p>
    </div>
  </div>

  <div class="stop" style="left:509px;top:517px;width:184px;height:184px">
    <svg class="icon" style="left:124px;top:20px"><use href="#ic-chat"/></svg>
    <div class="body" style="left:31px;top:12px;width:130px">
      <h3>Lorem ipsum</h3><div class="sub">LOREM IPSUM</div>
      <p>Lorem ipsum dolor sit amet, error regione voluptua mea ei, ei ullum civibus efficiantur pri. Ei exerci reprimique has. Duo te dicant complectitur, pri ei</p>
    </div>
  </div>

  <div class="stop" style="left:321px;top:358px;width:186px;height:186px">
    <svg class="icon" style="left:122px;top:32px"><use href="#ic-gears"/></svg>
    <div class="body" style="left:28px;top:30px;width:130px">
      <h3>Lorem ipsum</h3><div class="sub">LOREM IPSUM</div>
      <p>Lorem ipsum dolor sit amet, error regione voluptua mea ei, ei ullum civibus efficiantur pri. Ei exerci reprimique has. Duo te dicant complectitur, pri ei</p>
    </div>
  </div>

  <div class="stop" style="left:96px;top:309px;width:142px;height:142px">
    <div class="body" style="left:16px;top:18px;width:94px">
      <h3>Lorem ipsum</h3><div class="sub">LOREM IPSUM</div>
      <p>Lorem ipsum dolor sit amet, error regione voluptua mea ei, ei ullum</p>
    </div>
  </div>

  <div class="stop" style="left:79px;top:505px;width:264px;height:264px">
    <svg class="icon" style="left:106px;top:28px"><use href="#ic-flower"/></svg>
    <svg class="icon" style="left:138px;top:28px"><use href="#ic-globe"/></svg>
    <div class="body" style="left:30px;top:55px;width:174px">
      <h3>Lorem ipsum</h3><div class="sub">LOREM IPSUM</div>
      <p>Lorem ipsum dolor sit amet, error regione voluptua mea ei, ei ullum civibus efficiantur pri. Ei exerci reprimique has. Duo te dicant complectitur, pri ei nihil munere doctus. Vix id exerci verear, mea ea accusata petentium ullamcorper. Vel offendit percipit maluisset ea.</p>
    </div>
  </div>

  <div class="marker" style="left:437px;top:75px"><span class="day">10</span><span class="time">5:30pm</span></div>
  <div class="marker" style="left:652px;top:150px"><span class="day">11</span><span class="time">10:00am</span></div>
  <div class="marker" style="left:893px;top:275px"><span class="day">11</span><span class="time">6:00pm</span></div>
  <div class="marker" style="left:978px;top:462px"><span class="day">12</span><span class="time">8:00am</span></div>
  <div class="marker" style="left:908px;top:702px"><span class="day">12</span><span class="time">12:00pm</span></div>
  <div class="marker" style="left:700px;top:660px"><span class="day">12</span><span class="time">7:00pm</span></div>
  <div class="marker" style="left:447px;top:546px"><span class="day">13</span><span class="time">9:00am</span></div>
  <div class="marker" style="left:240px;top:410px"><span class="day">13</span><span class="time">5:00pm</span></div>
  <div class="marker" style="left:283px;top:550px"><span class="day">13</span><span class="time">1:00pm</span></div>

  <div class="legend">
    <div class="item" style="left:48px"><svg><use href="#ic-gears"/></svg>Lorem ipsum</div>
    <div class="item" style="left:264px"><svg><use href="#ic-chat"/></svg>Lorem ipsum</div>
    <div class="item" style="left:488px"><svg><use href="#ic-cloche"/></svg>Lorem ipsum</div>
    <div class="item" style="left:733px"><svg><use href="#ic-flower"/></svg>Lorem ipsum</div>
    <div class="item" style="left:962px"><svg><use href="#ic-globe"/></svg>Lorem ipsum</div>
  </div>
</div>
</body>
</html>
```